Our companies name is The Gilded Ladle and we specialize in craft cupcakes, what I mean by that is that we bake our cupcakes with craft beer and other alcoholic drinks. We are trying to focus on being elegant but at the same time unpretentious. Since we are incorporating beer in our cupcakes we want the business card to have our logo in the front and our information in the back.

Once we select the best design we will provide the contact information to be added. Thank you.

Industry/Entity Type

Business

Font styles to use
Decorative
Script

Requirements
Must have
• Round corners
Should not have
• Square corners

```html
<!DOCTYPE html>
<html lang="en">
<head>
<meta charset="utf-8">
<title>The Gilded Ladle – Business Card</title>
<link rel="stylesheet" href="https://fonts.googleapis.com/css2?family=Jura:wght@500;600;700&display=swap">
<style>
  :root {
    --stage: #d9d4cc;
    --card: #ece8e1;
    --ink: #1c1c1c;
    --ink-soft: #333333;
    --rule: #9a9690;
    --band-dark: #141414;
    --band-orange: #f05a22;
    --brand-dot: #1f2a30;
    --on-dark: #ffffff;
  }
  html, body {
    margin: 0;
    width: 1200px;
    height: 768px;
    overflow: hidden;
    background: var(--stage);
    font-family: "Jura", sans-serif;
  }
  .business-card {
    position: absolute;
    left: 100px;
    top: 91px;
    width: 1000px;
    height: 585px;
    border-radius: 30px;
    background: var(--card);
    overflow: hidden;
    box-shadow: 0 10px 30px rgba(0,0,0,0.12);
    color: var(--ink);
  }
  .brand {
    position: absolute;
    right: 76px;
    top: 128px;
    display: flex;
    align-items: center;
    gap: 16px;
  }
  .brand-dot {
    width: 34px;
    height: 34px;
    border-radius: 50%;
    background: var(--brand-dot);
  }
  .brand-name {
    font-size: 34px;
    font-weight: 700;
    color: var(--brand-dot);
    letter-spacing: 1px;
  }
  .person-name {
    position: absolute;
    left: 40px;
    top: 190px;
    margin: 0;
    font-size: 30px;
    font-weight: 600;
    letter-spacing: 1.5px;
  }
  .person-title {
    position: absolute;
    left: 40px;
    top: 242px;
    margin: 0;
    font-size: 22px;
    font-weight: 600;
  }
  .divider {
    position: absolute;
    left: 50px;
    top: 288px;
    width: 880px;
    height: 3px;
    background: linear-gradient(90deg, rgba(154,150,144,0.2), var(--rule) 25%, var(--rule) 75%, rgba(154,150,144,0.2));
  }
  .address {
    position: absolute;
    left: 40px;
    top: 380px;
    margin: 0;
    font-size: 22px;
    font-weight: 600;
    line-height: 32px;
    font-style: normal;
    color: var(--ink-soft);
  }
  .contact-list {
    position: absolute;
    right: 36px;
    top: 310px;
    margin: 0;
    padding: 0;
    list-style: none;
    text-align: right;
  }
  .contact-list li {
    display: flex;
    justify-content: flex-end;
    align-items: center;
    gap: 14px;
    font-weight: 600;
  }
  .contact-list .phone { font-size: 22px; height: 48px; letter-spacing: 1px; }
  .contact-list .web { font-size: 19px; height: 34px; }
  .contact-list svg { width: 22px; height: 22px; fill: var(--ink-soft); }
  .footer-bands {
    position: absolute;
    left: 0;
    bottom: 0;
    width: 1000px;
    height: 70px;
  }
  .footer-url {
    position: absolute;
    left: 40px;
    bottom: 14px;
    margin: 0;
    font-size: 20px;
    font-weight: 600;
    color: var(--on-dark);
    letter-spacing: 0.5px;
  }
</style>
</head>
<body>
  <div class="business-card">
    <div class="brand">
      <span class="brand-dot"></span>
      <span class="brand-name">The Gilded Ladle</span>
    </div>

    <h1 class="person-name">DANIEL WHITMORE</h1>
    <p class="person-title">Managing Director</p>
    <div class="divider"></div>

    <address class="address">27 Baker's Row, 4th floor<br>Kettle Lane NRV</address>

    <ul class="contact-list">
      <li class="phone">014 555 0192
        <svg viewBox="0 0 24 24"><path d="M6.6 10.8a15 15 0 0 0 6.6 6.6l2.2-2.2c.3-.3.7-.4 1-.2 1.1.4 2.3.6 3.6.6.6 0 1 .4 1 1V20c0 .6-.4 1-1 1A17 17 0 0 1 3 4c0-.6.4-1 1-1h3.5c.6 0 1 .4 1 1 0 1.3.2 2.5.6 3.6.1.3 0 .7-.2 1z"/></svg>
      </li>
      <li class="phone">014 555 0193
        <svg viewBox="0 0 24 24"><path d="M7 1h10a2 2 0 0 1 2 2v18a2 2 0 0 1-2 2H7a2 2 0 0 1-2-2V3a2 2 0 0 1 2-2zm0 3v15h10V4zm5 16.2a.9.9 0 1 0 0 1.8.9.9 0 0 0 0-1.8z"/></svg>
      </li>
      <li class="phone">014 555 0194
        <svg viewBox="0 0 24 24"><path d="M3 8h3v14H3zM8 2h9l3 3v17H8zm2 2v5h8V6l-2-2zm1 8v2h2v-2zm4 0v2h2v-2zm-4 4v2h2v-2zm4 0v2h2v-2z"/></svg>
      </li>
      <li class="web">hello@gildedladle.com
        <svg viewBox="0 0 24 24"><path d="M2 5h20v14H2zm2 2v.5l8 5.5 8-5.5V7zm0 2.9V17h16V9.9l-8 5.5z"/></svg>
      </li>
      <li class="web">www.gildedladle.com
        <svg viewBox="0 0 24 24"><path d="M12 2a10 10 0 1 0 0 20 10 10 0 0 0 0-20zm6.9 6h-3a15 15 0 0 0-1.3-3.9A8 8 0 0 1 18.9 8zM12 4c.8 1.1 1.5 2.5 1.9 4h-3.8c.4-1.5 1.1-2.9 1.9-4zM4.3 14a8 8 0 0 1 0-4h3.4a16 16 0 0 0 0 4zm.8 2h3a15 15 0 0 0 1.3 3.9A8 8 0 0 1 5.1 16zm3-8h-3a8 8 0 0 1 4.3-3.9C8.8 5.3 8.4 6.6 8.1 8zM12 20c-.8-1.1-1.5-2.5-1.9-4h3.8c-.4 1.5-1.1 2.9-1.9 4zm2.3-6H9.7a14 14 0 0 1 0-4h4.6a14 14 0 0 1 0 4zm.3 5.9c.6-1.2 1-2.5 1.3-3.9h3a8 8 0 0 1-4.3 3.9zm1.7-5.9a16 16 0 0 0 0-4h3.4a8 8 0 0 1 0 4z"/></svg>
      </li>
    </ul>

    <svg class="footer-bands" viewBox="0 0 1000 70" preserveAspectRatio="none" aria-hidden="true">
      <path d="M402 22 H1000 V70 H418 Q412 40 402 22 Z" fill="var(--band-orange)"/>
      <path d="M0 5 H388 Q408 5 414 30 L424 70 H0 Z" fill="var(--band-dark)"/>
    </svg>
    <p class="footer-url">www.gildedladle.com</p>
  </div>
</body>
</html>
```